Classy, Elegant, Simple Business Card Design

Looking to have a classy, simple, and elegant design. Want a top notch designed business card. I really like the look of the new torvane credit card. I also like the design I attached. I am trying to reach 21-29 year old females for booking us for there wedding or event. We offer Disc Jockey Service, Photo Booth Rentals, and Uplighting .

Target Market(s)

21-28 year old females

Contact Information for Business Card

Has to have logo, website, email, and phone number

Font styles to use
Other font styles liked:
• open to font choice, modern, clean
Designer to choose
33a6d7
0791cd
0555a3
ffffff

Requirements
Must have
• Has to have logo, website, email, and phone number
Nice to have
• I really like the design of the new torvane credit card. I also included my logo and some designs I like
Should not have
• clutter or too much info

```html
<!DOCTYPE html>
<html lang="en">
<head>
<meta charset="utf-8">
<title>Echoline Event Group – Business Card</title>
<link href="https://fonts.googleapis.com/css2?family=Josefin+Sans:wght@400&family=Roboto:wght@400;500;700&display=swap" rel="stylesheet">
<style>
  :root {
    --page-bg: #3a3a3c;
    --card-dark: #1d1e21;
    --brand-blue: #1560a8;
    --brand-bright: #0791cd;
    --brand-sky: #33a6d7;
    --brand-deep: #0555a3;
    --silver: #b9bcc2;
    --white: #ffffff;
    --muted: #8e9096;
  }
  * { margin: 0; padding: 0; box-sizing: border-box; }
  html, body { width: 799px; height: 1200px; overflow: hidden; }
  body {
    background: var(--page-bg);
    font-family: "Roboto", Arial, sans-serif;
    position: relative;
  }
  .card {
    position: absolute;
    left: 80px;
    width: 640px;
    height: 366px;
    background: var(--card-dark);
    border-radius: 4px;
    overflow: hidden;
    box-shadow: 0 10px 28px rgba(0,0,0,0.45);
  }
  .card--front { top: 130px; }
  .card--back { top: 704px; }

  .wordmark {
    position: absolute;
    font-family: "Josefin Sans", sans-serif;
    font-weight: 400;
    color: var(--brand-sky);
    text-align: center;
    letter-spacing: 0.08em;
    display: flex;
    align-items: center;
    gap: 12px;
  }
  .wordmark__dot {
    width: 14px; height: 14px; border-radius: 50%;
    background: var(--brand-bright);
    flex: none;
  }
  .wordmark__name { font-size: 34px; line-height: 1; }
  .wordmark__sub {
    display: block;
    font-size: 15px;
    letter-spacing: 0.42em;
    margin-top: 8px;
  }
  .card--front .wordmark { left: 0; right: 0; top: 120px; justify-content: center; }

  .equalizer-band {
    position: absolute;
    left: 0; right: 0; bottom: 0;
    height: 110px;
    background: linear-gradient(180deg, rgba(51,166,215,0) 0%, rgba(7,145,205,0.55) 60%, var(--brand-deep) 100%);
  }

  .back-art { position: absolute; inset: 0; }
  .card--back .wordmark { left: 34px; top: 120px; text-align: left; }

  .contact {
    position: absolute;
    left: 360px;
    top: 118px;
    color: var(--white);
  }
  .contact__name { font-size: 29px; font-weight: 700; line-height: 1.1; }
  .contact__role { font-size: 16px; margin-top: 2px; margin-bottom: 18px; }
  .contact__list { list-style: none; font-size: 17px; }
  .contact__list li { display: flex; align-items: center; gap: 12px; margin-bottom: 6px; }
  .contact__list svg { width: 16px; height: 16px; flex: none; }
</style>
</head>
<body>

<section class="card card--front" aria-label="Card front">
  <div class="wordmark">
    <span class="wordmark__dot"></span>
    <div>
      <span class="wordmark__name">ECHOLINE</span>
      <span class="wordmark__sub">EVENT GROUP</span>
    </div>
  </div>
  <div class="equalizer-band" role="img" aria-label="Blue sound equalizer bars along the bottom edge"></div>
</section>

<section class="card card--back" aria-label="Card back">
  <svg class="back-art" viewBox="0 0 640 366" preserveAspectRatio="none" aria-hidden="true">
    <path d="M318 0 C262 120 214 280 140 366 L160 366 C232 280 282 120 340 0 Z" fill="var(--silver)"/>
    <path d="M340 0 C282 120 232 280 160 366 L640 366 L640 0 Z" fill="var(--brand-blue)"/>
  </svg>

  <div class="wordmark">
    <span class="wordmark__dot"></span>
    <div>
      <span class="wordmark__name">ECHOLINE</span>
      <span class="wordmark__sub">EVENT GROUP</span>
    </div>
  </div>

  <div class="contact">
    <h1 class="contact__name">Daniel Reyes</h1>
    <p class="contact__role">Founder &amp; CEO</p>
    <ul class="contact__list">
      <li>
        <svg viewBox="0 0 16 16" aria-hidden="true"><path fill="#fff" d="M2 5c0-2 2-3 6-3s6 1 6 3v1h-3V5H5v1H2zM4 7h8l2 6H2z"/><circle cx="8" cy="10" r="1.6" fill="#1560a8"/></svg>
        555 0142 0142
      </li>
      <li>
        <svg viewBox="0 0 16 16" aria-hidden="true"><rect x="1" y="3" width="14" height="10" fill="#fff"/><path d="M1 3l7 6 7-6" fill="none" stroke="#1560a8" stroke-width="1.4"/></svg>
        daniel@echoline.com
      </li>
      <li>
        <svg viewBox="0 0 16 16" aria-hidden="true"><circle cx="8" cy="8" r="7" fill="#fff"/><path d="M1 8h14M8 1c-3 4-3 10 0 14M8 1c3 4 3 10 0 14" fill="none" stroke="#1560a8" stroke-width="1"/></svg>
        www.echoline.com
      </li>
    </ul>
  </div>
</section>

</body>
</html>
```